Crestline Plaque & Medal Unique Business Card Design

Recently selected a new logo design and waiting to recieve print files. I've attached image for your review. We are a trophies and awards company that provides engraving on trophies, plaques, name plates, name tags, desk sets, medals, acrylics, and signage.

We are located in Monroe, Louisiana and provide this service with computerized & laser engraving equipment.

Target Market(s)

Corporate, Sport, Church, and Special Events

Industry/Entity Type

Business

Contact Information for Business Card

I'd like to see the following list on the card: Trophies, Plaques, Name Plates, Name Tags, Desk Sets, Medals, Certificates... this is accomplished with Computerized & Laser Engraving

Colors
0555a3
ec1f27
ffffff

Requirements
Must have
• I like either single or double sided. If a design can be created with a frosted card stock I'd consider single. Must be Red, White, and Blue. Dwight Palmer - Owner, 412 W 8th Ave, Monroe, La 71208 office 318-555-0148 fax 318-555-0163 email: info@crestlineplaquemedal.example, and website: www.crestlineplaquemedal.example

```html
<!DOCTYPE html>
<html lang="en">
<head>
<meta charset="utf-8">
<title>Crestline Plaque &amp; Medal — Business Card</title>
<link href="https://fonts.googleapis.com/css2?family=Montserrat:wght@400;600&display=swap" rel="stylesheet">
<style>
  :root {
    --backdrop: #3b3430;
    --card: #161616;
    --brand-blue: #0555a3;
    --bright-blue: #2f7fd6;
    --brand-red: #ec1f27;
    --white: #ffffff;
    --muted: #e6e6e6;
  }
  * { box-sizing: border-box; margin: 0; padding: 0; }
  html, body { width: 1200px; height: 780px; overflow: hidden; }
  body {
    background: var(--backdrop);
    font-family: "Montserrat", sans-serif;
    display: flex;
    align-items: center;
    justify-content: center;
    gap: 40px;
  }
  .card {
    width: 560px;
    height: 320px;
    background: var(--card);
    border-radius: 4px;
    position: relative;
    box-shadow: 0 14px 30px rgba(0,0,0,.45);
    color: var(--white);
  }
  .brand {
    display: flex;
    align-items: center;
    gap: 12px;
    font-weight: 600;
    color: var(--bright-blue);
    letter-spacing: .5px;
  }
  .brand-dot {
    width: 14px; height: 14px;
    border-radius: 50%;
    background: var(--brand-red);
    flex: none;
  }
  .card-front { display: flex; align-items: center; justify-content: center; }
  .card-front .brand { font-size: 32px; }

  .card-back .brand {
    position: absolute;
    top: 52px; right: 44px;
    font-size: 26px;
  }
  .contact {
    position: absolute;
    left: 40px; top: 138px;
    width: 230px;
    text-align: right;
  }
  .contact-name {
    font-size: 20px;
    font-weight: 600;
    color: var(--bright-blue);
  }
  .contact-role { font-size: 14px; margin-bottom: 16px; }
  .contact-line {
    display: flex;
    justify-content: flex-end;
    align-items: center;
    gap: 8px;
    font-size: 13px;
    line-height: 22px;
  }
  .contact-icon {
    width: 16px; height: 16px;
    background: var(--brand-blue);
    border-radius: 2px;
    display: flex; align-items: center; justify-content: center;
  }
  .divider {
    position: absolute;
    left: 292px; top: 148px;
    width: 2px; height: 130px;
    background: var(--white);
  }
  .services {
    position: absolute;
    left: 312px; top: 150px;
    list-style: none;
    font-size: 15px;
    line-height: 21px;
  }
</style>
</head>
<body>
  <section class="card card-front">
    <div class="brand"><span class="brand-dot"></span>Crestline Plaque &amp; Medal</div>
  </section>

  <section class="card card-back">
    <div class="brand"><span class="brand-dot"></span>Crestline Plaque &amp; Medal</div>

    <div class="contact">
      <p class="contact-name">Employee Name</p>
      <p class="contact-role">Managing Director</p>
      <p class="contact-line">0012 3456 789
        <span class="contact-icon"><svg width="10" height="10" viewBox="0 0 10 10"><path d="M2 1h2l1 2-1 1a5 5 0 0 0 2 2l1-1 2 1v2a1 1 0 0 1-1 1A8 8 0 0 1 1 2a1 1 0 0 1 1-1z" fill="#fff"/></svg></span>
      </p>
      <p class="contact-line">info@youremail.com
        <span class="contact-icon"><svg width="10" height="10" viewBox="0 0 10 10"><rect x="1" y="2" width="8" height="6" fill="none" stroke="#fff"/><path d="M1 2l4 3 4-3" fill="none" stroke="#fff"/></svg></span>
      </p>
      <p class="contact-line">www.yourwebsite.com
        <span class="contact-icon"><svg width="10" height="10" viewBox="0 0 10 10"><circle cx="5" cy="5" r="4" fill="none" stroke="#fff"/><path d="M1 5h8M5 1c-2 2-2 6 0 8M5 1c2 2 2 6 0 8" fill="none" stroke="#fff" stroke-width=".7"/></svg></span>
      </p>
    </div>

    <div class="divider"></div>

    <ul class="services">
      <li>engraving on trophies</li>
      <li>plaques</li>
      <li>name plates</li>
      <li>name tags, desk sets</li>
      <li>medals</li>
      <li>acrylics and signage</li>
    </ul>
  </section>
</body>
</html>
```